Poster Design Project

We are launching a new company Q Vyn, we sell advertising on digital signage and we are launching our company selling ads at our 2 locations, Marlow Bend Sports and Rec Club and the Torrand Isle Sports and Rec Club. We want to advertise that we have 5 10 and 15 ad slots available and ads start from as little as $27.00 per week. We need to let people know we offer 10% discount to WBTGA members. it needs to have the following contact details to get more information, Gideon 0427359042 and gideon@qvyn.com.au. As a new launch we are offering for the first 10 customers one of 2 discounts, get 4 weeks free all you have to pay is the content creation fee ($99 for 5 second ad) or 4 weeks free and free content creation if you sign up to a 18 week contract.

Update: need the add to start wit something like this but you can be creative:

Need to get you message or brand out, Have you heard of digital sinage?
We have ads avaliable starting from $27 per week at one of our locations.

Or something like that, as i am introducing my company they dont know what i do you untill they read this poster.

Target Market(s)

Targeting small to medium buisness

Industry/Entity Type

Advertising

Requirements
Must have
• Logo

```html
<!DOCTYPE html>
<html lang="en">
<head>
<meta charset="utf-8">
<title>Q Vyn – Digital Signage Ads</title>
<link rel="stylesheet" href="https://fonts.googleapis.com/css2?family=Archivo+Black&family=Play:wght@400;700&display=swap">
<style>
  :root {
    --paper: #ffffff;
    --lime: #a8ff00;
    --slate: #474747;
    --ink: #0d0d0d;
    --price-green: #2ee81a;
    --teal: #1094b4;
    --white: #ffffff;
  }
  html, body {
    margin: 0;
    padding: 0;
    overflow: hidden;
    background: var(--paper);
  }
  .poster {
    position: relative;
    width: 848px;
    height: 1200px;
    overflow: hidden;
    background: var(--paper);
    font-family: "Play", sans-serif;
    color: var(--ink);
  }
  .backdrop {
    position: absolute;
    inset: 0;
    width: 848px;
    height: 1200px;
  }
  .brand {
    position: absolute;
    left: 78px;
    top: 150px;
    display: flex;
    align-items: center;
    gap: 20px;
  }
  .brand-mark {
    width: 64px;
    height: 64px;
    background: var(--ink);
  }
  .brand-name {
    font-family: "Archivo Black", sans-serif;
    font-size: 84px;
    line-height: 1;
    color: var(--ink);
  }
  .intro {
    position: absolute;
    left: 74px;
    top: 300px;
    width: 600px;
  }
  .intro-hook {
    margin: 0 0 10px;
    font-family: "Archivo Black", sans-serif;
    font-weight: 400;
    font-size: 27px;
    line-height: 1.2;
  }
  .intro-places {
    margin: 0;
    font-size: 20px;
    line-height: 1.3;
  }
  .offer {
    position: absolute;
    left: 74px;
    top: 462px;
    margin: 0;
    font-size: 35px;
    line-height: 1.2;
    white-space: nowrap;
  }
  .offer .heavy {
    font-family: "Archivo Black", sans-serif;
    font-size: 33px;
  }
  .offer .price {
    font-family: "Archivo Black", sans-serif;
    font-size: 38px;
    color: var(--price-green);
    text-shadow: 1px 2px 2px rgba(0,0,0,0.45);
  }
  .member-deal {
    position: absolute;
    left: 0;
    right: 0;
    top: 722px;
    margin: 0;
    text-align: center;
    font-family: "Archivo Black", sans-serif;
    font-weight: 400;
    font-size: 70px;
    line-height: 1.08;
    letter-spacing: 1px;
    color: var(--ink);
    text-shadow: 2px 4px 5px rgba(0,0,0,0.4);
  }
  .member-deal .accent { color: var(--teal); }
  .launch {
    position: absolute;
    left: 48px;
    top: 900px;
    width: 400px;
  }
  .launch-title {
    margin: 0 0 8px;
    font-family: "Archivo Black", sans-serif;
    font-weight: 400;
    font-size: 22px;
    line-height: 1.2;
  }
  .launch-list {
    margin: 0;
    padding-left: 22px;
    font-size: 19px;
    line-height: 1.3;
  }
  .launch-list li { margin-bottom: 6px; }
  .contact {
    position: absolute;
    right: 52px;
    top: 1030px;
    text-align: right;
    color: var(--white);
    font-size: 27px;
    line-height: 1.45;
  }
  .contact p { margin: 0; }
</style>
</head>
<body>
<main class="poster">
  <svg class="backdrop" viewBox="0 0 707 1000" preserveAspectRatio="none" aria-hidden="true">
    <defs>
      <linearGradient id="middle-fold" x1="0" y1="0" x2="1" y2="1">
        <stop offset="0" stop-color="#b4ff2a"/>
        <stop offset="0.55" stop-color="#98e000"/>
        <stop offset="1" stop-color="#7cc200"/>
      </linearGradient>
      <linearGradient id="fold-shadow" x1="0" y1="0" x2="1" y2="0">
        <stop offset="0" stop-color="#000" stop-opacity="0.18"/>
        <stop offset="1" stop-color="#000" stop-opacity="0"/>
      </linearGradient>
    </defs>
    <polygon class="panel-right" points="707,5 707,1000 190,1000" fill="var(--lime)"/>
    <polygon class="panel-middle" points="0,430 707,760 707,1000 200,1000" fill="url(#middle-fold)"/>
    <polygon class="panel-left-shadow" points="0,420 14,428 345,1000 330,1000" fill="url(#fold-shadow)"/>
    <polygon class="panel-left" points="0,430 330,1000 0,1000" fill="var(--lime)"/>
    <polygon class="panel-corner" points="707,760 707,1000 300,1000" fill="var(--slate)"/>
  </svg>

  <header class="brand">
    <span class="brand-mark"></span>
    <span class="brand-name">Q Vyn</span>
  </header>

  <section class="intro">
    <p class="intro-hook">Need to get your message or brand out?<br>Have you heard of digital signage?</p>
    <p class="intro-places">Your ad on screen at Marlow Bend Sports and Rec Club<br>and Torrand Isle Sports and Rec Club.</p>
  </section>

  <p class="offer">5 10 and 15 ad <span class="heavy">slots available</span> and<br>ads start from as little as<br><span class="price">$27.00</span> per week</p>

  <h1 class="member-deal"><span class="accent">10% discount</span> to<br>WBTGA members</h1>

  <section class="launch">
    <h2 class="launch-title">Launch offer – first 10 customers</h2>
    <ul class="launch-list">
      <li>4 weeks free – just pay the content creation fee ($99 for a 5 second ad)</li>
      <li>4 weeks free plus free content creation on an 18 week contract</li>
    </ul>
  </section>

  <footer class="contact">
    <p>Gideon</p>
    <p>0427359042</p>
    <p>gideon@qvyn.com.au</p>
  </footer>
</main>
</body>
</html>
```